Banner 170x60 for Barrel Sauna Rental Banner

Attention, please do every side graphic distance 5cm . It is for attachment.
search for a graphic design in dimension 170x60cm.
we have a barrel sauna rental service and need a banner for the two sides.
please look photos.
big text is: (I CAN RENT ME!!! )in english like: you can rent me
heisse-holzstube.de
015243197720
info@heisse-holzstube.de
we need an eye catcher design!!!!
Design:
maybe wood in at background.
maybe burning fire and sauna style.
Please don't use my barrell sauna pictures. It is only an example for you what we do. The barrel sauna is on build at the moment.

```html
<!DOCTYPE html>
<html lang="de">
<head>
<meta charset="utf-8">
<title>Mich kann man mieten – Fassauna Banner</title>
<link href="https://fonts.googleapis.com/css2?family=Oswald:wght@400;500&display=swap" rel="stylesheet">
<style>
  :root {
    --text-white: #ffffff;
    --accent-amber: #ffb000;
    --wood-dark: #1a0f08;
    --wood-mid: #4a2c18;
    --wood-warm: #6b3d1e;
    --fire-orange: #e8560a;
    --fire-glow: #ff9a1a;
  }
  html, body {
    margin: 0;
    padding: 0;
    width: 1200px;
    height: 424px;
    overflow: hidden;
    background: #000;
  }
  .banner {
    position: relative;
    width: 1200px;
    height: 424px;
    overflow: hidden;
    font-family: 'Oswald', sans-serif;
  }
  .banner__backdrop {
    position: absolute;
    inset: 0;
    background:
      linear-gradient(180deg, rgba(0,0,0,0.95) 0%, rgba(0,0,0,0) 22%),
      linear-gradient(180deg, transparent 62%, rgba(232,86,10,0.55) 84%, var(--fire-glow) 100%),
      radial-gradient(ellipse at 85% 75%, rgba(255,140,20,0.5), transparent 45%),
      radial-gradient(ellipse at 10% 92%, rgba(255,120,10,0.6), transparent 40%),
      repeating-linear-gradient(90deg, var(--wood-mid) 0 92px, var(--wood-dark) 92px 96px),
      var(--wood-warm);
  }
  .banner__content {
    position: absolute;
    inset: 0;
    color: var(--text-white);
  }
  .line {
    position: absolute;
    left: 0;
    right: 0;
    margin: 0;
    text-align: center;
    white-space: nowrap;
    line-height: 1;
    transform-origin: center top;
  }
  .accent { color: var(--accent-amber); }
  .headline {
    top: 53px;
    font-size: 96px;
    font-weight: 500;
    letter-spacing: 6px;
    transform: scaleX(0.86);
  }
  .website {
    top: 168px;
    font-size: 60px;
    font-weight: 400;
    letter-spacing: 2px;
  }
  .phone {
    top: 225px;
    font-size: 89px;
    font-weight: 500;
    letter-spacing: 0;
  }
  .email {
    top: 324px;
    font-size: 44px;
    font-weight: 400;
    letter-spacing: 1px;
    transform: scaleX(0.82);
  }
</style>
</head>
<body>
  <div class="banner">
    <div class="banner__backdrop" role="img" aria-label="Dunkle Holzbretter mit lodernden Flammen am unteren Rand"></div>
    <div class="banner__content">
      <h1 class="line headline">MICH KANN MAN <span class="accent">MIETEN!!!</span></h1>
      <div class="line website">www.<span class="accent">heisse-holzstube</span>.de</div>
      <div class="line phone">015243197720</div>
      <div class="line email">info@heisse-holzstube.de</div>
    </div>
  </div>
</body>
</html>
```